business card deign

Logo needs the following on it.
1. attached logo
2. Tagline - "If it keeps a drink cold or the party going...we do it!"
3. Name- Dalton Pikes, Founder and CPO
4. Address - 412 E. Carver Avenue, Ste 2207, Tampa, FL. 33917
5. Phone - 555.318.4726

```html
<!DOCTYPE html>
<html lang="en">
<head>
<meta charset="utf-8">
<title>Chillbay Business Card</title>
<link rel="stylesheet" href="https://fonts.googleapis.com/css2?family=Montserrat:wght@400;600;700&display=swap">
<style>
  :root {
    --bg: #161616;
    --card: #2a2a2a;
    --ink: #f2f2f2;
    --ink-soft: #e4e4e4;
  }
  html, body {
    margin: 0;
    padding: 0;
    width: 1200px;
    height: 1059px;
    overflow: hidden;
    background: var(--bg);
    font-family: "Montserrat", sans-serif;
    color: var(--ink);
  }
  .canvas { position: relative; width: 1200px; height: 1059px; }
  .card {
    position: absolute;
    width: 690px;
    height: 392px;
    background: var(--card);
    border-radius: 18px;
  }
  .card--front { left: 257px; top: 89px; }
  .card--back { left: 255px; top: 547px; }

  .identity {
    position: absolute;
    right: calc(690px - 322px);
    top: 170px;
    text-align: right;
  }
  .identity__name {
    font-weight: 700;
    font-size: 24px;
    letter-spacing: 0.5px;
    margin: 0;
    line-height: 1;
  }
  .identity__role {
    font-weight: 400;
    font-size: 15px;
    margin: 6px 0 0;
    color: var(--ink-soft);
  }
  .divider {
    position: absolute;
    left: 343px;
    top: 148px;
    width: 1px;
    height: 95px;
    background: var(--ink-soft);
  }
  .contact {
    position: absolute;
    left: 369px;
    top: 145px;
    font-size: 15.5px;
    color: var(--ink-soft);
    line-height: 1;
  }
  .contact__address { margin: 0; line-height: 22px; }
  .contact__line {
    display: flex;
    align-items: center;
    gap: 8px;
    margin-top: 11px;
    margin-left: -3px;
  }
  .contact__address + .contact__line { margin-top: 14px; }
  .contact__icon { width: 12px; height: 12px; fill: var(--ink-soft); flex: none; }

  .brand {
    position: absolute;
    left: 0;
    right: 0;
    top: 242px;
    text-align: center;
    font-weight: 600;
    font-size: 44px;
    letter-spacing: 18px;
    padding-left: 18px;
    margin: 0;
    line-height: 1;
  }
  .tagline {
    position: absolute;
    left: 0;
    right: 0;
    top: 342px;
    text-align: center;
    font-size: 15px;
    color: var(--ink-soft);
    margin: 0;
  }
</style>
</head>
<body>
<main class="canvas">
  <section class="card card--front">
    <div class="identity">
      <h1 class="identity__name">DALTON PIKES</h1>
      <p class="identity__role">Founder and CPO</p>
    </div>
    <div class="divider"></div>
    <div class="contact">
      <p class="contact__address">412 E. Carver Avenue<br>Ste 2207, Tampa, FL. 33917</p>
      <div class="contact__line">
        <svg class="contact__icon" viewBox="0 0 12 12" aria-hidden="true"><path d="M1 4.5C1 2.5 3.5 1.5 6 1.5S11 2.5 11 4.5L9 5V3.8H3V5ZM3 6h6l1.5 4.5h-9Z"/></svg>
        <span>555.318.4726</span>
      </div>
      <div class="contact__line">
        <svg class="contact__icon" viewBox="0 0 12 12" aria-hidden="true"><path d="M1 5 6 1.5 11 5V11H1Zm1 .6V10h8V5.6L6 8.4Z"/></svg>
        <span>daltonpikes@mailbox.com</span>
      </div>
    </div>
  </section>

  <section class="card card--back">
    <p class="brand">CHILLBAY</p>
    <p class="tagline">If it keeps a drink cold or the party going...we do it!</p>
  </section>
</main>
</body>
</html>
```